GlassHaven Artbook for Okanagan Region, British Columbia

Creating an art book: GlassHaven, for the Okanagan Wine Region in British Columbia, Canada. Would like smart, modern, clean and linear...cool, sexy urban, not ugly boring suburban... I need a cover that appeals to the wino in all of us! Title: GlassHaven -Marla Dovicki
Updates
Thank you all kindly for your efforts. I have added some files so that you can get a sense of my aesthetic...it's never easy trying to figure it out, is it? I will hopefully have dimensions of book soon...cheers, Marla
would anyone please design a giant wine bottle with the wine label that looks like a label but says glasshaven...just curious to see if it works as a design or not...thank you.
Target Market(s)
Designing this wine art book of quotes to wineries in Okanagan BC. Buyer is wine lover and tourist ready to spend his vacation bucks on this wonderful book!
Look and feel

```html
<!DOCTYPE html>
<html lang="en">
<head>
<meta charset="utf-8">
<title>GlassHaven — Marla Dovicki</title>
<link rel="stylesheet" href="https://fonts.googleapis.com/css2?family=Big+Shoulders+Display:wght@300;500&display=swap">
<style>
  :root {
    --paper: #a69e9b;
    --paper-light: #dedad7;
    --bottle-dark: #000000;
    --bottle-glass: #36b02a;
    --title-pink: #e24aa6;
    --author-white: #ffffff;
  }
  * { margin: 0; padding: 0; box-sizing: border-box; }
  html, body {
    width: 938px;
    height: 1200px;
    overflow: hidden;
  }
  .cover {
    position: relative;
    width: 938px;
    height: 1200px;
    background:
      radial-gradient(ellipse 430px 320px at 470px 1080px, var(--paper-light) 0%, rgba(222,218,215,0) 100%),
      var(--paper);
    overflow: hidden;
  }
  .bottle-art {
    position: absolute;
    inset: 0;
    width: 938px;
    height: 1200px;
  }
  .title {
    position: absolute;
    inset: 0;
    width: 938px;
    height: 1200px;
  }
  .title-text {
    font-family: "Big Shoulders Display", "Arial Narrow", sans-serif;
    font-weight: 300;
    font-size: 180px;
    fill: none;
    stroke: var(--title-pink);
    stroke-width: 4;
  }
  .author {
    position: absolute;
    left: 578px;
    top: 996px;
    font-family: "Big Shoulders Display", "Arial Narrow", sans-serif;
    font-weight: 500;
    font-size: 66px;
    letter-spacing: 2px;
    line-height: 1;
    color: var(--author-white);
    text-transform: uppercase;
    white-space: nowrap;
  }
</style>
</head>
<body>
  <main class="cover">
    <svg class="bottle-art" viewBox="0 0 938 1200" role="img" aria-label="Upside-down dark wine bottle with a green glass neck">
      <rect class="bottle-art-body" x="329" y="0" width="299" height="810" fill="var(--bottle-dark)"/>
      <rect class="bottle-art-neck" x="424" y="810" width="112" height="286" fill="var(--bottle-glass)"/>
    </svg>

    <svg class="title" viewBox="0 0 938 1200" aria-labelledby="cover-title">
      <text id="cover-title" class="title-text"
        transform="translate(412 38) rotate(90)"
        textLength="690" lengthAdjust="spacingAndGlyphs">GLASSHAVEN</text>
    </svg>

    <p class="author">Marla Dovicki</p>
  </main>
</body>
</html>
```